Website Re-design for Kids Playhouse Business

Need current website which looks very outdated to be re-designed to look modern and contemporary, reduce clutter significantly and make it look elegant and simple.
Current website: http://www.tumblenest.com.au/
A website which the business owner likes, use as reference/inspiration: http://vexa.com.au/
Looking for light green palette, natural colours. "WHAT'S ON" page/link no longer required.
Industry/Entity Type
Business
Number of Pages Required
5+ page
Look and feel
Each slider illustrates characteristics of the customer's brand and the style your logo design should communicate.

```html
<!DOCTYPE html>
<html lang="en">
<head>
<meta charset="utf-8">
<title>Tumble Nest Playhouse &amp; Cafe</title>
<link rel="stylesheet" href="https://fonts.googleapis.com/css2?family=Fredoka:wght@500;600&family=Lato:wght@400;700&display=swap">
<style>
:root{
  --green:#8cd21c;
  --green-soft:#a9dc5a;
  --leaf:#4f8a2a;
  --leaf-deep:#3f7322;
  --sage:#6f9a45;
  --ink:#1d1d1d;
  --body:#5a5a5a;
  --grey-bg:#f2f1ec;
  --white:#ffffff;
  --header:rgba(30,30,30,.82);
}
*{box-sizing:border-box;margin:0;padding:0}
html,body{width:1200px;height:3098px;overflow:hidden}
body{font-family:"Lato",sans-serif;color:var(--body);background:var(--white);position:relative}
h1,h2{font-family:"Fredoka",sans-serif;font-weight:500}

/* hero */
.hero{position:absolute;left:0;top:0;width:1200px;height:677px;
  background:linear-gradient(135deg,#d8cfc4 0%,#b9a895 35%,#e8e2da 60%,#a99683 100%)}
.site-header{position:absolute;left:0;top:0;width:1200px;height:124px;background:var(--header)}
.brand{position:absolute;left:80px;top:46px;display:flex;align-items:center;gap:10px}
.brand-mark{width:30px;height:30px;background:var(--green)}
.brand-name{font-family:"Lato",sans-serif;font-weight:700;font-size:22px;color:var(--white)}
.main-nav{position:absolute;left:281px;top:48px;display:flex;gap:30px;font-size:16px;line-height:20px;color:var(--white);font-weight:700}
.main-nav span{display:block}
.main-nav .single{padding-top:10px}
.main-nav .current{color:var(--green)}
.hero-box{position:absolute;left:223px;top:335px;width:752px;height:156px;background:rgba(255,255,255,.72)}
.hero-title{position:absolute;left:223px;top:370px;width:752px;text-align:center;font-size:54px;line-height:64px;color:var(--leaf)}
.btn{display:inline-flex;align-items:center;justify-content:center;border-radius:30px;font-size:21px;font-family:"Lato",sans-serif}
.hero-btn{position:absolute;left:508px;top:456px;width:178px;height:60px;background:var(--green);color:var(--white)}

/* intro band */
.intro{position:absolute;left:0;top:677px;width:1200px;height:155px;background:var(--green)}
.intro p{position:absolute;left:80px;top:24px;width:790px;font-size:15.5px;line-height:26px;color:var(--white)}
.intro p em{font-style:normal;color:var(--leaf-deep);font-weight:700}
.intro-btn{position:absolute;left:890px;top:48px;width:188px;height:56px;background:var(--white);color:var(--green)}

/* about */
.about-title{position:absolute;left:80px;top:890px;font-size:37px;color:var(--ink)}
.accent{color:var(--leaf)}
.about-text{position:absolute;left:80px;top:964px;width:560px;font-size:13px;line-height:25.4px}
.about-photo-lg{position:absolute;left:760px;top:896px;width:364px;height:364px;border-radius:50%;border:8px solid var(--sage);
  background:linear-gradient(160deg,#f3e6cf,#dcc9a2 50%,#c9dcb4)}
.about-photo-sm{position:absolute;left:665px;top:1053px;width:206px;height:206px;border-radius:50%;border:7px solid var(--green);
  background:linear-gradient(160deg,#4c7f5a,#5f9a3f 70%,#d9b64a)}

/* features */
.feature-band{position:absolute;left:0;top:1324px;width:1200px;height:262px;background:linear-gradient(90deg,#6f9a45,#86b05a 60%,#6f9a45)}
.feature-title{position:absolute;left:0;top:1384px;width:1200px;text-align:center;font-size:36px;color:var(--white)}
.feature-text{position:absolute;left:186px;top:1448px;width:828px;text-align:center;font-size:13.5px;line-height:25px;color:var(--white)}
.card{position:absolute;width:509px;height:291px}
.card-caption{position:absolute;left:10px;right:10px;bottom:10px;height:64px;background:rgba(25,25,25,.72);
  color:var(--white);font-weight:700;font-size:19px;display:flex;align-items:center;justify-content:center}
.card-birthday{left:78px;top:1586px;background:linear-gradient(135deg,#7a9cb8,#c9a27a 55%,#e6c07a)}
.card-holiday{left:613px;top:1586px;background:linear-gradient(180deg,#e6ecea 0%,#6fb24a 55%,#4f9536)}
.card-rooms{left:78px;top:1898px;background:linear-gradient(135deg,#8fa86a,#d9c79a 45%,#7fb0a5)}
.card-specials{left:613px;top:1898px;background:linear-gradient(135deg,#b58a5a,#f0d7a6 55%,#a9c07a)}

/* contact */
.contact{position:absolute;left:0;top:2282px;width:1200px;height:605px;background:var(--grey-bg)}
.contact-title{position:absolute;left:0;top:2344px;width:1200px;text-align:center;font-size:37px;color:var(--ink)}
.contact-lede{position:absolute;left:250px;top:2398px;width:700px;text-align:center;font-size:13.5px;line-height:27px}
.field{position:absolute;left:78px;width:571px;background:var(--white);border:1px solid #d8d8d8;border-radius:3px;
  font-size:13px;color:#666;padding:14px 12px}
.submit{position:absolute;left:78px;top:2755px;width:571px;height:49px;background:var(--green);color:var(--white);
  font-size:19px;display:flex;align-items:center;justify-content:center;border-radius:2px}
.info{position:absolute;left:704px;width:419px;height:79px;background:var(--white);border-left:4px solid var(--green)}
.info svg{position:absolute;left:16px;top:15px}
.info h4{position:absolute;left:52px;top:14px;font-size:16px;color:var(--leaf);font-weight:700}
.info p{position:absolute;left:52px;top:40px;font-size:13.5px;color:#555}

/* footer */
.site-footer{position:absolute;left:0;top:2887px;width:1200px;height:211px;background:var(--leaf)}
.footer-brand{position:absolute;left:0;top:2936px;width:1200px;display:flex;justify-content:center;align-items:center;gap:10px}
.footer-brand .brand-mark{background:var(--white)}
.copyright{position:absolute;left:78px;top:2984px;font-size:13.5px;color:var(--white)}
.footer-nav{position:absolute;left:0;top:3028px;width:1200px;text-align:center;font-size:14.5px;color:var(--white)}
.footer-nav span{margin:0 10px}
.social{position:absolute;left:962px;top:2975px;display:flex;gap:4px}
.social span{width:37px;height:37px;border-radius:50%;border:2px solid var(--white);display:block}
.social span.filled{background:var(--green)}
</style>
</head>
<body>

<section class="hero" role="img" aria-label="Children playing with toy kitchen and table in a bright indoor playroom"></section>
<header class="site-header">
  <div class="brand"><span class="brand-mark"></span><span class="brand-name">Tumble Nest</span></div>
  <nav class="main-nav">
    <span class="single current">Home</span>
    <span>Hours<br>&amp; Price</span>
    <span>Party<br>Packages</span>
    <span>Party<br>Rooms</span>
    <span>Vacation<br>care</span>
    <span>School<br>Holiday Program</span>
    <span>Specials<br>&amp; Promotion</span>
    <span class="single">Gallery</span>
  </nav>
</header>
<div class="hero-box"></div>
<h1 class="hero-title">So much Fun for everyone</h1>
<span class="btn hero-btn">CONTACT US</span>

<section class="intro">
  <p>We pride ourselves in offering the best indoor play centre for your kids to engage in fun and learning activities in a specially created environment that is not only warm and safe but also enhances and stimulates creativity and curiosity in a child. Tumble Nest offers variety of kids party venues like our themed <em>party rooms</em> which are hand painted.</p>
  <span class="btn intro-btn">CONTACT US</span>
</section>

<h2 class="about-title">About <span class="accent">Tumble Nest Playhouse &amp; Cafe</span></h2>
<p class="about-text">Tumble Nest is an indoor Kids Play Centre and Cafe that offers both kids and adults a chance to enjoy their time, together! We pride ourselves in offering the best indoor play centre for your kids to engage in fun and learning activities in a specially created environment that is not only warm and safe but also enhances and stimulates creativity and curiosity in a child. Tumble Nest offers variety of kids party venues like our themed party rooms which are hand painted.<br>Tumble Nest has entertained over 1 million children. Our party rooms are unarguably the best in Sydney and were designed by an internationally renowned artist who was commissioned from England and has won numerous awards. She was specially flown to Australia to design and hand paint our party rooms.</p>
<div class="about-photo-lg" role="img" aria-label="Children in party hats celebrating at a birthday table"></div>
<div class="about-photo-sm" role="img" aria-label="Toddler playing in a colourful ball pit"></div>

<section class="feature-band" role="img" aria-label="Green tinted background of children at play"></section>
<h2 class="feature-title">Our Feature</h2>
<p class="feature-text">Tumble Nest has entertained over 1 million children. Our party rooms are unarguably the best in Sydney and were designed by an internationally renowned artist who was commissioned from England and has won numerous awards. She was specially flown to Australia to design and hand paint our party rooms.</p>

<div class="card card-birthday" role="img" aria-label="Children at a birthday party in a painted party room"><div class="card-caption">Perfect venue for birthdays and private parties</div></div>
<div class="card card-holiday" role="img" aria-label="Child bouncing on a hopper ball on a grass field"><div class="card-caption">We host school holiday programs</div></div>
<div class="card card-rooms" role="img" aria-label="Smiling child surrounded by party balloons"><div class="card-caption">4 kids loving party rooms themes</div></div>
<div class="card card-specials" role="img" aria-label="Children with a costumed mascot"><div class="card-caption">Exclusive specials &amp; promotions</div></div>

<section class="contact"></section>
<h2 class="contact-title">Our <span class="accent">Contact</span></h2>
<p class="contact-lede">Lorem ipsum dolor sit amet, consectetur adipisicing elit, sed do eiusmod tempor incididunt ut labore<br>et dolore magna aliqua. Ut enim ad minim veniam, quis nostrud</p>

<div class="field" style="top:2486px;height:48px">Name* :</div>
<div class="field" style="top:2544px;height:48px">Phone* :</div>
<div class="field" style="top:2602px;height:48px">Email* :</div>
<div class="field" style="top:2660px;height:80px">Comment / Question :</div>
<div class="submit">SUBMIT NOW</div>

<div class="info" style="top:2486px">
  <svg width="22" height="26" viewBox="0 0 22 26"><path d="M11 1a8 8 0 0 0-8 8c0 6 8 15 8 15s8-9 8-15a8 8 0 0 0-8-8z" fill="#8cd21c"/><circle cx="11" cy="9" r="3" fill="#fff"/></svg>
  <h4>Office Address</h4><p>41 Wattle Lane Brookvale 2100 NSW Australia.</p>
</div>
<div class="info" style="top:2602px">
  <svg width="22" height="22" viewBox="0 0 24 24"><path d="M6.6 10.8a15 15 0 0 0 6.6 6.6l2.2-2.2a1 1 0 0 1 1-.25 11.4 11.4 0 0 0 3.6.57 1 1 0 0 1 1 1V20a1 1 0 0 1-1 1A17 17 0 0 1 3 4a1 1 0 0 1 1-1h3.5a1 1 0 0 1 1 1c0 1.25.2 2.45.57 3.57a1 1 0 0 1-.25 1z" fill="#8cd21c"/></svg>
  <h4>Call us</h4><p>02 5550 0142</p>
</div>
<div class="info" style="top:2726px">
  <svg width="24" height="18" viewBox="0 0 24 18"><rect x="1" y="1" width="22" height="16" rx="1" fill="#8cd21c"/><path d="M2 2l10 8 10-8" stroke="#fff" stroke-width="2" fill="none"/></svg>
  <h4>Message Us</h4><p>hello@tumblenestplay.com</p>
</div>

<footer class="site-footer"></footer>
<div class="footer-brand"><span class="brand-mark"></span><span class="brand-name">Tumble Nest</span></div>
<p class="copyright">© 2018 www.tumblenest.com.au .All Right Reserved</p>
<nav class="footer-nav"><span>Home</span>|<span>About</span>|<span>Our Features</span>|<span>Contact</span></nav>
<div class="social" aria-label="Social links"><span class="filled"></span><span></span><span></span><span></span></div>

</body>
</html>
```